Plakat-Design für Wartezimmer von Zahnarztpraxen
Vielen Dank! Eine super Zusammenarbeit! Ich würde es jederzeit wiederholen.
Zielgruppe
Wir sind ein Zahnärztlicher Berufsverband. Das Poster soll an unsere Mitglieder verteilt werden, so dass es in Wartezimmern von Zahnarztpraxen hängen wird.
Aufgabenstellung
Wir wollen einen Eyecatcher fürs Wartezimmer im Din A 1-Format.
Das Design soll im Pop-Art-Stil sein. Bitte den Entwurf im Anhang beachten. Dies beschreibt das gewünschte Poster schon sehr gut, allerdings ist es noch deutlich verbesserbar :-)
Idee : Maske ab, Mund auf (soll provozieren) und über den Stern das 'Kleingedruckte' die Message an die Patienten weitergeben:
Nur zur Behandlung bei Ihrem Zahnarzt. Trotz Pandemie immer für Sie da! Denn gesund beginnt im Mund.
Der Mund aus dem Entwurf gefällt uns sehr gut und kommt von der Plenzo-Bildersuche. (ist allerdings zu erwerben)
Evtl. Die Farben anpassen an die Farben unseres Verbandes: www.bvkq.de
das Dokument unseres Verbandes gebe ich dazu, es muss allerdings ergänzt werden um: Landesverband KR

```html
<!DOCTYPE html>
<html lang="de">
<head>
<meta charset="utf-8">
<title>Maske ab – Mund auf · Wartezimmer-Plakat</title>
<link href="https://fonts.googleapis.com/css2?family=Bangers&family=Comic+Neue:wght@700&family=Archivo:wght@400;800&display=swap" rel="stylesheet">
<style>
  :root{
    --cream:#f1eada;
    --red:#e3001b;
    --red-deep:#b3000f;
    --mouth-dark:#2a0004;
    --lip:#d0101e;
    --yellow:#fff200;
    --orange:#f7a21b;
    --ink:#111;
    --olive:#7b7a5c;
    --blue:#1d4f92;
    --grey:#8a8a80;
  }
  *{margin:0;padding:0;box-sizing:border-box}
  html,body{width:908px;height:1200px;overflow:hidden;background:var(--cream)}
  .poster{position:relative;width:908px;height:1200px;background:var(--cream)}
  .stage{position:absolute;left:28px;top:25px;width:852px;height:957px;overflow:hidden;
    background:radial-gradient(ellipse at 50% 48%, #f0101f 0%, var(--red) 45%, var(--red-deep) 100%)}
  .mouth{position:absolute;left:183px;top:172px;width:490px;height:640px;border-radius:50%;
    background:radial-gradient(ellipse at 50% 50%, var(--mouth-dark) 0%, #5a0008 52%, var(--lip) 66%, rgba(227,0,27,0) 74%)}
  .headline{position:absolute;left:0;top:0;width:852px;height:957px;pointer-events:none}
  .headline span{position:absolute;font-family:"Bangers",system-ui,sans-serif;line-height:1;white-space:nowrap;
    letter-spacing:4px;transform:rotate(-7deg) skewX(-10deg);
    background:linear-gradient(100deg,var(--orange),var(--yellow) 60%);-webkit-background-clip:text;background-clip:text;-webkit-text-fill-color:transparent;
    filter:drop-shadow(-5px 5px 0 var(--ink)) drop-shadow(2px -2px 0 var(--ink))}
  .line-1{left:108px;top:268px;font-size:190px}
  .line-2{left:150px;top:428px;font-size:175px}
  .asterisk{position:absolute;left:700px;top:420px;font-family:"Archivo",sans-serif;font-weight:800;font-size:78px;color:var(--ink)}
  .footnote{position:absolute;left:70px;top:955px;width:443px;height:140px;
    background:linear-gradient(90deg,#ffb500,var(--orange));border:3px solid var(--ink);box-shadow:-5px 5px 0 var(--ink);
    padding:12px 10px 0 32px;font-family:"Comic Neue",cursive;font-weight:700;font-size:24px;letter-spacing:1.1px;line-height:27px;color:var(--ink);white-space:nowrap}
  .footnote-star{position:absolute;left:-24px;top:-30px;font-family:"Archivo",sans-serif;font-weight:800;font-size:60px;line-height:1;color:#fff;
    -webkit-text-stroke:3px var(--ink)}
  .url{position:absolute;left:170px;top:1120px;width:250px;text-align:center;font-family:"Comic Neue",cursive;font-weight:700;font-size:25px;letter-spacing:0.5px;color:var(--ink)}
  .sender{position:absolute;left:549px;top:1004px;width:320px;font-family:"Archivo",sans-serif}
  .sender-mark{display:flex;align-items:flex-start;gap:18px}
  .sender-square{width:58px;height:84px;border:3px solid var(--olive);margin-top:6px}
  .sender-name{font-weight:800;font-size:24px;letter-spacing:1px;line-height:31px;color:var(--olive)}
  .tagline{margin-top:8px;font-size:24px;color:var(--blue);white-space:nowrap}
  .claims{margin-top:0;font-size:19.5px;color:var(--grey);white-space:nowrap}
</style>
</head>
<body>
<main class="poster">
  <section class="stage">
    <div class="mouth" role="img" aria-label="Fotografie eines weit geöffneten Mundes mit roten Lippen und weißen Zähnen im Pop-Art-Raster"></div>
    <h1 class="headline">
      <span class="line-1">MASKE AB</span>
      <span class="line-2">MUND AUF</span>
    </h1>
    <div class="asterisk">*</div>
  </section>

  <aside class="footnote">
    <span class="footnote-star">*</span>
    Nur zur Behandlung bei Ihrem<br>Zahnarzt. Trotz Pandemie<br>immer für Sie da! Denn<br>gesund beginnt im Mund.
  </aside>
  <p class="url">www.bvkq.de</p>

  <footer class="sender">
    <div class="sender-mark">
      <div class="sender-square"></div>
      <p class="sender-name">Bund Vereinter<br>Kieferpraxen<br>e.V.</p>
    </div>
    <p class="tagline">Ihre Interessenvertretung</p>
    <p class="claims">politisch - fachlich - wirtschaftlich</p>
  </footer>
</main>
</body>
</html>
```